Crestline Plaque & Medal Unique Business Card Design

Recently selected a new logo design and waiting to recieve print files. I've attached image for your review. We are a trophies and awards company that provides engraving on trophies, plaques, name plates, name tags, desk sets, medals, acrylics, and signage.

We are located in Monroe, Louisiana and provide this service with computerized & laser engraving equipment.

Target Market(s)

Corporate, Sport, Church, and Special Events

Industry/Entity Type

Business

Contact Information for Business Card

I'd like to see the following list on the card: Trophies, Plaques, Name Plates, Name Tags, Desk Sets, Medals, Certificates... this is accomplished with Computerized & Laser Engraving

Colors
0555a3
ec1f27
ffffff

Requirements
Must have
• I like either single or double sided. If a design can be created with a frosted card stock I'd consider single. Must be Red, White, and Blue. Dwight Palmer - Owner, 412 W 8th Ave, Monroe, La 71208 office 318-555-0148 fax 318-555-0163 email: info@crestlineplaquemedal.example, and website: www.crestlineplaquemedal.example

```html
<!DOCTYPE html>
<html lang="en">
<head>
<meta charset="utf-8">
<title>Crestline Plaque &amp; Medal — Business Card</title>
<link rel="stylesheet" href="https://fonts.googleapis.com/css2?family=Lato:wght@400;700&display=swap">
<style>
  :root {
    --page-bg: #ecebe8;
    --blue-light: #1f7fcc;
    --blue-mid: #1c64b8;
    --blue-deep: #1f3f94;
    --brand-blue: #0555a3;
    --brand-red: #ec1f27;
    --white: #ffffff;
    --paper: #f4f4f4;
  }
  * { box-sizing: border-box; margin: 0; padding: 0; }
  html, body {
    width: 1200px;
    height: 900px;
    overflow: hidden;
    background: var(--page-bg);
    font-family: "Lato", sans-serif;
  }
  .sheet {
    width: 1200px;
    height: 900px;
    display: flex;
    flex-direction: column;
    align-items: center;
    justify-content: center;
    gap: 56px;
  }
  .card {
    position: relative;
    width: 600px;
    height: 343px;
    overflow: hidden;
    box-shadow: 0 6px 18px rgba(0, 0, 0, 0.18);
  }

  /* Back side */
  .card-back {
    background: radial-gradient(ellipse at 45% 20%, var(--blue-light) 0%, var(--blue-mid) 45%, var(--blue-deep) 100%);
    display: flex;
    flex-direction: column;
    align-items: center;
    justify-content: center;
    gap: 22px;
    color: var(--white);
  }
  .brand {
    display: flex;
    align-items: center;
    gap: 14px;
    font-weight: 700;
    white-space: nowrap;
  }
  .brand-dot {
    width: 26px;
    height: 26px;
    border-radius: 50%;
  }
  .card-back .brand { font-size: 38px; }
  .card-back .brand-dot { background: var(--white); }
  .services {
    width: 470px;
    padding-top: 12px;
    border-top: 1.5px solid var(--white);
    text-align: center;
    font-size: 14px;
    line-height: 1.5;
  }
  .services-note { font-size: 13px; opacity: 0.9; }

  /* Front side */
  .card-front { background: var(--paper); }
  .front-top {
    height: 168px;
    background: linear-gradient(180deg, var(--white) 0%, #eeeeee 100%);
    display: flex;
    align-items: center;
    justify-content: center;
    padding-left: 90px;
  }
  .card-front .brand { color: var(--brand-blue); font-size: 34px; }
  .card-front .brand-dot { background: var(--brand-red); width: 22px; height: 22px; }

  .front-band {
    position: absolute;
    left: 0; right: 0; bottom: 0;
    height: 175px;
    background: linear-gradient(180deg, var(--blue-light) 0%, var(--blue-mid) 50%, var(--blue-deep) 100%);
    color: var(--white);
    display: flex;
    padding: 26px 0 0 0;
  }
  .person {
    width: 275px;
    text-align: right;
    padding-right: 24px;
  }
  .person-name { font-size: 25px; font-weight: 700; line-height: 1.1; }
  .person-title { font-size: 17px; margin-top: 4px; }
  .person-address { font-size: 19px; line-height: 1.3; margin-top: 14px; }

  .contact-list {
    list-style: none;
    font-size: 15px;
    line-height: 1;
    display: flex;
    flex-direction: column;
    gap: 8px;
    padding-top: 2px;
    white-space: nowrap;
  }
  .contact-item { display: flex; align-items: center; gap: 8px; }
  .contact-icon {
    width: 17px;
    height: 17px;
    background: var(--brand-red);
    border-radius: 3px;
    flex: none;
  }
</style>
</head>
<body>
<main class="sheet">

  <section class="card card-back" aria-label="Card back">
    <div class="brand">
      <span class="brand-dot"></span>
      <span class="brand-name">Crestline Plaque &amp; Medal</span>
    </div>
    <div class="services">
      <p>Trophies · Plaques · Name Plates · Name Tags · Desk Sets · Medals · Certificates</p>
      <p class="services-note">Computerized &amp; Laser Engraving</p>
    </div>
  </section>

  <section class="card card-front" aria-label="Card front">
    <div class="front-top">
      <div class="brand">
        <span class="brand-dot"></span>
        <span class="brand-name">Crestline Plaque &amp; Medal</span>
      </div>
    </div>

    <div class="front-band">
      <div class="person">
        <p class="person-name">Dwight Palmer</p>
        <p class="person-title">Owner</p>
        <p class="person-address">412 W 8th Ave<br>Monroe, La 71208</p>
      </div>

      <ul class="contact-list">
        <li class="contact-item">
          <svg class="contact-icon" viewBox="0 0 17 17" aria-hidden="true">
            <path d="M5 4 h2 l1 3 -1.4 1 a6 6 0 0 0 2.4 2.4 l1-1.4 3 1 v2 a1 1 0 0 1 -1 1 A8 8 0 0 1 4 5 a1 1 0 0 1 1-1z" fill="#fff"/>
          </svg>
          <span>318-555-0148</span>
        </li>
        <li class="contact-item">
          <svg class="contact-icon" viewBox="0 0 17 17" aria-hidden="true">
            <rect x="5" y="3.5" width="7" height="4" fill="#fff"/>
            <rect x="3.5" y="7" width="10" height="5" rx="1" fill="#fff"/>
            <rect x="5.5" y="10" width="6" height="3.5" fill="#fff" stroke="#ec1f27" stroke-width="0.8"/>
          </svg>
          <span>318-555-0163</span>
        </li>
        <li class="contact-item">
          <svg class="contact-icon" viewBox="0 0 17 17" aria-hidden="true">
            <rect x="3.5" y="5" width="10" height="7" fill="#fff"/>
            <path d="M3.5 5 l5 4 5-4" fill="none" stroke="#ec1f27" stroke-width="1"/>
          </svg>
          <span>info@crestlineplaquemedal.example</span>
        </li>
        <li class="contact-item">
          <svg class="contact-icon" viewBox="0 0 17 17" aria-hidden="true">
            <g fill="none" stroke="#fff" stroke-width="1.6">
              <rect x="3.5" y="7.5" width="6" height="3.5" rx="1.7" transform="rotate(-45 6.5 9.25)"/>
              <rect x="7.5" y="5.5" width="6" height="3.5" rx="1.7" transform="rotate(-45 10.5 7.25)"/>
            </g>
          </svg>
          <span>www.crestlineplaquemedal.example</span>
        </li>
      </ul>
    </div>
  </section>

</main>
</body>
</html>
```